4D Cradle Glimpse Luxury Ultrasound Billboard

Design a HIGH-END, MODERN billboard for my private prenatal ultrasound studio, 4D Cradle Glimpse, located in Pace, Florida.
This billboard will be viewed by drivers traveling at highway speeds, so it must be extremely clean, simple, and readable within 6 seconds.
About My Business
4D Cradle Glimpse is a private prenatal ultrasound studio specializing in:
Highest technology 4D/HD Ultrasounds
Early Gender Determination
Pregnancy Confirmation
I have been serving families for nearly 10 years and is known for creating a memorable experience, not just an ultrasound appointment.
Design Style
I DO NOT want:
Flowers
Leaves
Swirls
Glitter
Hearts everywhere
Busy backgrounds
Generic maternity stock graphics
I DO want:
Modern
Luxury
Upscale
Clean
Professional
Eye-catching
Premium medical spa feel
Colors
Use colors from my logo:
LOGO Green ( or a deep green)
Black
White
Soft Gold accents
Images:
Incorporate my professional headshot in a clean, modern way, logo, and the ultrasound images
Text
Keep wording minimal.
Primary Headline ( OPEN TO IDEAS) :
EXAMPLES ( WOULD RATHER SOMETHING MORE CATCHY)
" ADVANCED IMAGING. UNFORGETTABLE MOMENTS"
"MEET YOUR BABY BEFORE BIRTH"
Under headline:
4D Ultrasound • Early Gender • Pregnancy Confirmation
Business Name:
4D Cradle Glimpse
Private Prenatal Ultrasound Studio
Phone Number:
850-471-5923
Important
This billboard must be readable in 5–6 seconds from a moving vehicle.
Less text is better.
The phone number and business name must be visible from a distance.
The design should feel like a premium brand that immediately tells expecting parents:
“This is where I go to see my baby.”
Files Provided
Official logo
Headshot
Ultrasound images
Don’t make this look like a medical office billboard.
Make it look like a luxury baby experience billboard. That’s what separates 4D Cradle Glimpse from hospitals, OB offices, and all the new studios popping up around you. The emotional connection is what gets moms to book. ❤️
Billboard Size - 10.6” x 36”

```html
<!DOCTYPE html>
<html lang="en">
<head>
<meta charset="UTF-8">
<title>4D Cradle Glimpse Billboard</title>
<link rel="stylesheet" href="https://fonts.googleapis.com/css2?family=Montserrat:wght@600;700&family=Poppins:wght@500;600&display=swap">
<style>
  :root {
    --page: #f2f2f0;
    --black: #050505;
    --white: #ffffff;
    --gold-light: #f1d48f;
    --gold: #d3aa5a;
    --gold-deep: #a9833c;
    --grey-text: #8d8d8d;
    --studio-green: #2f5a35;
  }
  * { box-sizing: border-box; margin: 0; padding: 0; }
  html, body { width: 1200px; height: 1046px; overflow: hidden; }
  body {
    background: var(--page);
    display: flex;
    align-items: center;
    justify-content: center;
    font-family: "Montserrat", sans-serif;
  }
  .billboard {
    position: relative;
    width: 1140px;
    height: 336px;
    background: var(--black);
    overflow: hidden;
  }
  .phone-band {
    position: absolute;
    left: 200px;
    top: 273px;
    width: 570px;
    height: 63px;
    background: var(--white);
  }
  .portrait-art {
    position: absolute;
    left: 0;
    top: 0;
  }
  .headline {
    position: absolute;
    left: 352px;
    top: 6px;
    font-weight: 700;
    line-height: 1;
    background: linear-gradient(180deg, var(--gold-light) 0%, var(--gold) 55%, var(--gold-deep) 100%);
    -webkit-background-clip: text;
    background-clip: text;
    color: transparent;
  }
  .headline .line-main { display: block; font-size: 74px; letter-spacing: 0.5px; }
  .headline .line-sub { display: block; font-size: 60px; margin-top: 8px; }
  .services {
    position: absolute;
    left: 352px;
    top: 176px;
    list-style: none;
    font-family: "Poppins", sans-serif;
    font-weight: 600;
    font-size: 16.5px;
    color: var(--white);
  }
  .services li {
    display: flex;
    align-items: center;
    gap: 8px;
    height: 27.5px;
  }
  .services svg { width: 19px; height: 19px; }
  .phone-number {
    position: absolute;
    left: 342px;
    top: 276px;
    width: 330px;
    text-align: center;
    font-weight: 700;
    font-size: 46px;
    line-height: 58px;
    color: var(--black);
    letter-spacing: 0.5px;
  }
  .scan-frame {
    position: absolute;
    left: 694px;
    top: 190px;
    width: 148px;
    height: 148px;
    border-radius: 50%;
    border: 4px solid var(--white);
    background: radial-gradient(circle at 50% 45%, #c07a66 0%, #9a5040 55%, #5a2a20 100%);
  }
  .studio-name {
    position: absolute;
    left: 880px;
    top: 214px;
    width: 240px;
    text-align: center;
  }
  .studio-name .brand {
    display: block;
    font-weight: 700;
    font-size: 26px;
    line-height: 1.1;
    color: var(--gold);
  }
  .studio-name .tagline {
    display: block;
    margin-top: 12px;
    font-weight: 600;
    font-size: 9.5px;
    letter-spacing: 0.6px;
    color: var(--grey-text);
  }
</style>
</head>
<body>
  <main class="billboard">
    <div class="phone-band"></div>

    <svg class="portrait-art" width="340" height="336" viewBox="0 0 340 336">
      <defs>
        <linearGradient id="portraitTone" x1="0" y1="0" x2="1" y2="1">
          <stop offset="0" stop-color="#e9e6e1"/>
          <stop offset="0.55" stop-color="#c9b79c"/>
          <stop offset="1" stop-color="#3d5a3e"/>
        </linearGradient>
        <linearGradient id="ribbonGold" x1="0" y1="0" x2="0" y2="1">
          <stop offset="0" stop-color="#f1d48f"/>
          <stop offset="0.5" stop-color="#c99a48"/>
          <stop offset="1" stop-color="#e6c47b"/>
        </linearGradient>
      </defs>
      <path class="gold-ribbon" d="M185 0 L200 0 Q424 168 228 336 L205 336 Q409 168 185 0 Z" fill="url(#ribbonGold)"/>
      <path class="headshot" role="img" aria-label="Professional headshot of the studio owner holding an ultrasound probe" d="M0 0 L185 0 Q409 168 205 336 L0 336 Z" fill="url(#portraitTone)"/>
    </svg>

    <h1 class="headline">
      <span class="line-main">Meet Your Baby</span>
      <span class="line-sub">Before Birth</span>
    </h1>

    <ul class="services">
      <li><svg viewBox="0 0 20 20"><rect x="1.5" y="3.5" width="14" height="14" rx="2" fill="none" stroke="#d3aa5a" stroke-width="2"/><path d="M5 10 L8.5 13.5 L18 3" fill="none" stroke="#d3aa5a" stroke-width="2.6" stroke-linecap="round" stroke-linejoin="round"/></svg>4D Ultrasound</li>
      <li><svg viewBox="0 0 20 20"><rect x="1.5" y="3.5" width="14" height="14" rx="2" fill="none" stroke="#d3aa5a" stroke-width="2"/><path d="M5 10 L8.5 13.5 L18 3" fill="none" stroke="#d3aa5a" stroke-width="2.6" stroke-linecap="round" stroke-linejoin="round"/></svg>Pregnancy Confirmation</li>
      <li><svg viewBox="0 0 20 20"><rect x="1.5" y="3.5" width="14" height="14" rx="2" fill="none" stroke="#d3aa5a" stroke-width="2"/><path d="M5 10 L8.5 13.5 L18 3" fill="none" stroke="#d3aa5a" stroke-width="2.6" stroke-linecap="round" stroke-linejoin="round"/></svg>Early Gender</li>
    </ul>

    <p class="phone-number">850·471·5923</p>

    <div class="scan-frame" role="img" aria-label="4D ultrasound image of twin babies"></div>

    <div class="studio-name">
      <span class="brand">4D Cradle Glimpse</span>
      <span class="tagline">PRENATAL ULTRASOUND STUDIO</span>
    </div>
  </main>
</body>
</html>
```